Book cover for book about Climate Change

Looking for a clean, bold, and attractive cover for a mass-market paperback (5.5"x 8.5") about solving the climate change problem. Title is either "Where the Rivers Meet” or A Harbor Made of Glass” (your choice), subtitle is "A practical field guide to mending the weather — so that the young ones after us inherit steady seasons and open skies," author is Lorne Whitcombe. Thinking that it *might* feature an image of Earth (or a portion thereof) and its very thin layer of atmosphere -- but STRONGLY encourage other ideas too!

Requirements
Nice to have
• Keep it positive — NOT scary doom-and-gloom

```html
<!DOCTYPE html>
<html lang="en">
<head>
<meta charset="utf-8">
<title>A Harbor Made of Glass — Lorne Whitcombe</title>
<link rel="stylesheet" href="https://fonts.googleapis.com/css2?family=Bebas+Neue&family=Montserrat:wght@700;800&display=swap">
<style>
  :root {
    --page: #ffffff;
    --plum: #3d1033;
    --gold: #f3b71b;
    --snow: #fbfbfd;
  }
  * { margin: 0; padding: 0; box-sizing: border-box; }
  html, body {
    width: 1200px; height: 1200px; overflow: hidden;
    background: var(--page);
  }
  .cover {
    position: absolute; left: 280px; top: 100px;
    width: 660px; height: 1020px;
    background: radial-gradient(circle at 95% 30%, #4a1840 0%, var(--plum) 35%);
  }
  .author {
    position: absolute; top: 58px; left: 0; right: 0;
    display: flex; align-items: center; justify-content: center; gap: 22px;
  }
  .author-rule { flex: 1; height: 2px; background: var(--snow); }
  .author-name {
    font-family: "Montserrat", sans-serif; font-weight: 800;
    font-size: 40px; letter-spacing: 4px; color: var(--gold);
    white-space: nowrap; line-height: 1;
  }
  .title {
    position: absolute; top: 128px; left: 0; right: 0;
    font-family: "Bebas Neue", sans-serif; font-weight: 400;
    font-size: 210px; line-height: 170px; text-align: center;
    color: var(--snow);
  }
  .title-line { display: flex; justify-content: center; align-items: center; height: 170px; }
  .title-line--gold { color: var(--gold); font-size: 200px; }
  .globe {
    display: inline-block; width: 128px; height: 146px; margin: 0 4px;
    border-radius: 50%;
    background: radial-gradient(circle at 40% 40%, #ffffff 0%, #e9e6ec 60%, #cfc6d2 100%);
    transform: translateY(-4px);
  }
  .subtitle {
    position: absolute; top: 856px; left: 0; right: 0;
    font-family: "Montserrat", sans-serif; font-weight: 700;
    font-size: 19px; line-height: 30px; text-align: center;
    color: var(--snow); text-transform: uppercase;
  }
  .subtitle em { font-style: normal; color: var(--gold); }
</style>
</head>
<body>
  <main class="cover">
    <div class="author">
      <span class="author-rule"></span>
      <span class="author-name">LORNE WHITCOMBE</span>
      <span class="author-rule"></span>
    </div>
    <h1 class="title">
      <span class="title-line">A</span>
      <span class="title-line title-line--gold">HARB<span class="globe" role="img" aria-label="Illustration of planet Earth standing in for the letter O"></span>R</span>
      <span class="title-line">MADE OF</span>
      <span class="title-line">GLASS</span>
    </h1>
    <p class="subtitle">
      A practical <em>field guide</em> to <em>mending</em><br>
      the weather — so that the young ones<br>
      after us inherit steady seasons<br>
      and open skies.
    </p>
  </main>
</body>
</html>
```